business card

Business card for new business.
Red and black corporate colors.
Card can have an Indsutrial feel to it. Feel free to add Rust, Bolted steel, or graphics as you see fit. We provide highly specialized services to the below mentioned industries.
Keep information out of corners so that if I want I can choose rounded corners.
Information
- front. name - title - phone - email
- Rear
Refining - Rail - Infrastructure - Mining - Power
Redcliff - Stonebridge - Fort Ashcroft - Millbrook - Westhaven

```html
<!DOCTYPE html>
<html lang="en">
<head>
<meta charset="utf-8">
<title>Ironvale Business Card</title>
<link href="https://fonts.googleapis.com/css2?family=Roboto:wght@400;500&family=Roboto+Condensed:wght@400;700&display=swap" rel="stylesheet">
<style>
  :root {
    --backdrop: #5a4838;
    --card-white: #f1f1f1;
    --brand-red: #e60012;
    --steel-grey: #7d7d7d;
    --text-grey: #808080;
    --white: #ffffff;
    --black: #000000;
  }
  * { margin: 0; padding: 0; box-sizing: border-box; }
  html, body { width: 1200px; height: 960px; overflow: hidden; }
  body {
    position: relative;
    background: var(--backdrop);
    font-family: "Roboto", sans-serif;
  }
  .card {
    position: absolute;
    width: 600px;
    height: 343px;
    box-shadow: 1px 2px 3px rgba(0,0,0,0.45);
    overflow: hidden;
  }
  /* Front */
  .card-front { left: 314px; top: 113px; background: var(--card-white); }
  .brand-name {
    position: absolute;
    left: 0; right: 0; top: 123px;
    text-align: center;
    font-family: "Roboto Condensed", sans-serif;
    font-weight: 700;
    font-size: 50px;
    letter-spacing: 1px;
    color: var(--text-grey);
    line-height: 1;
  }
  .person {
    position: absolute;
    left: 0; right: 0; top: 244px;
    text-align: center;
    font-family: "Roboto Condensed", sans-serif;
    line-height: 1;
  }
  .person-name { font-weight: 700; font-size: 24px; color: var(--brand-red); }
  .person-title { font-weight: 400; font-size: 16px; color: var(--text-grey); }
  .contact-bar {
    position: absolute;
    left: 0; right: 0; top: 291px; height: 52px;
    background: var(--steel-grey);
    border-top: 5px solid var(--brand-red);
  }
  .contact-item {
    position: absolute;
    top: 0;
    transform: translateX(-50%);
    text-align: center;
    color: var(--white);
    font-size: 15px;
    white-space: nowrap;
  }
  .contact-icon {
    position: absolute;
    left: 50%; top: -16px;
    width: 26px; height: 26px;
    margin-left: -13px;
    border-radius: 50%;
    background: var(--white);
    display: flex; align-items: center; justify-content: center;
  }
  .contact-text { display: block; padding-top: 16px; }
  .contact-phone { left: 117px; }
  .contact-email { left: 283px; }
  .contact-web { left: 464px; }
  /* Back */
  .card-back { left: 312px; top: 472px; background: var(--brand-red); }
  .brand-name-back {
    position: absolute;
    left: 0; right: 0; top: 128px;
    text-align: center;
    font-family: "Roboto Condensed", sans-serif;
    font-weight: 700;
    font-size: 40px;
    letter-spacing: 1px;
    color: var(--white);
    line-height: 1;
  }
  .services {
    position: absolute;
    left: 0; right: 0; top: 256px;
    text-align: center;
    font-size: 15px;
    line-height: 18px;
  }
  .services-line {
    display: inline-block;
    background: linear-gradient(90deg, var(--white) 0%, var(--white) 40%, var(--black) 85%);
    -webkit-background-clip: text;
    background-clip: text;
    color: transparent;
  }
</style>
</head>
<body>
  <section class="card card-front">
    <div class="brand-name">IRONVALE</div>
    <div class="person">
      <span class="person-name">DANIEL BROOKS</span><span class="person-title">– CEO/FOUNDER</span>
    </div>
    <div class="contact-bar">
      <div class="contact-item contact-phone">
        <span class="contact-icon">
          <svg width="12" height="12" viewBox="0 0 24 24" aria-hidden="true"><path fill="#e60012" d="M6.6 10.8a15.2 15.2 0 0 0 6.6 6.6l2.2-2.2c.3-.3.7-.4 1-.2 1.1.4 2.3.6 3.6.6.6 0 1 .4 1 1V20c0 .6-.4 1-1 1A17 17 0 0 1 3 4c0-.6.4-1 1-1h3.5c.6 0 1 .4 1 1 0 1.3.2 2.5.6 3.6.1.3 0 .7-.2 1z"/></svg>
        </span>
        <span class="contact-text">555 210 4478</span>
      </div>
      <div class="contact-item contact-email">
        <span class="contact-icon">
          <svg width="12" height="12" viewBox="0 0 24 24" aria-hidden="true"><path fill="#e60012" d="M2 5h20v14H2z"/><path fill="none" stroke="#fff" stroke-width="2" d="M2 6l10 7 10-7"/></svg>
        </span>
        <span class="contact-text">info@ironvale.com</span>
      </div>
      <div class="contact-item contact-web">
        <span class="contact-icon">
          <svg width="12" height="12" viewBox="0 0 24 24" aria-hidden="true"><circle cx="12" cy="12" r="10" fill="#e60012"/><path fill="none" stroke="#fff" stroke-width="1.6" d="M2 12h20M12 2c3 3 3 17 0 20M12 2c-3 3-3 17 0 20"/></svg>
        </span>
        <span class="contact-text">www.ironvale.com</span>
      </div>
    </div>
  </section>

  <section class="card card-back">
    <div class="brand-name-back">IRONVALE</div>
    <div class="services">
      <span class="services-line">Drilling • Pipeline • Construction • Forestry</span><br>
      <span class="services-line">Power • Redcliff • Stonebridge • Fort Ashcroft</span><br>
      <span class="services-line">Millbrook • Westhaven</span>
    </div>
  </section>
</body>
</html>
```